Wordpress Design Project for Bankruptcy Law Office in San Francisco

our current website: www.dorvanelilaw-example.com

we would like to re-design it for wordpress to make it faster and a bit more modern.

content should be similar to what we have there right now but also we do family law

please include logo for law office:

Law Office of Marta K. Dolvenidze

Thank you.
Updates

please see attached word document with logos that we like as an example.

we do tend to like color red.  darker red.

Please submit your design variations and logo as soon as possible.   We would like to go over them and make our decision

Reason: Please create couple of more variations of logo for your design, so we can make our decision what we like the most. Please see word doc for samples: Text: Law Office Of Marta K. Dolvenidze

Reason: final touches

Target Market(s)

bankruptcy and family law clients

Industry/Entity Type

Family Law

Requirements
Must have
• see examples of law sites
http://promo.lexorbin-example.com/testimonials

- new logo: Law Office of Marta K. Dolvenidze
- client intake form
- blog
- contact us form

Nice to have
• - map
- red color
- on the front page a nice photo of SF or a happy family

```html
<!DOCTYPE html>
<html lang="en">
<head>
<meta charset="utf-8">
<title>Law Office of Marta K. Dolvenidze</title>
<link rel="stylesheet" href="https://fonts.googleapis.com/css2?family=Cinzel:wght@400&family=Oswald:wght@400&family=PT+Sans:wght@400;700&family=Alfa+Slab+One&display=swap">
<style>
:root{
  --red:#b3161c;
  --red-dark:#8e1015;
  --red-deep:#5c0a0c;
  --nav:#4e0708;
  --card:#d40c18;
  --ink:#2a2a2a;
  --heading:#b3161c;
  --bg:#e9e9e9;
  --white:#fff;
  --yellow:#ffd400;
}
*{box-sizing:border-box;margin:0;padding:0}
html,body{width:1096px;height:1200px;overflow:hidden}
body{background:var(--bg);font-family:"PT Sans",sans-serif;color:var(--ink);position:relative}
.page{position:absolute;left:105px;top:18px;width:886px;height:1157px;background:var(--white);box-shadow:0 0 14px rgba(0,0,0,.35)}
.abs{position:absolute}

.site-header{left:0;top:0;width:886px;height:99px;background:linear-gradient(90deg,var(--red-dark),var(--red) 45%,#a3171b 75%,#7a1a14)}
.brand{left:12px;top:14px;display:flex;align-items:center;gap:10px}
.brand-mark{width:95px;height:74px;background:var(--red-deep)}
.brand-name{font-family:"Cinzel",serif;color:var(--white);font-weight:400;line-height:1.1}
.brand-name .small{display:block;font-size:23px;letter-spacing:1px;padding-left:100px}
.brand-name .big{display:block;font-size:33px;letter-spacing:1.5px}
.phone{right:10px;top:60px;display:flex;align-items:center;gap:8px;color:var(--white);font-family:"Cinzel",serif;font-size:24px}
.phone-icon{width:24px;height:24px;background:#f1f1f1;border-radius:3px;display:flex;align-items:center;justify-content:center}

.main-nav{left:0;top:99px;width:886px;height:40px;background:var(--nav);display:flex;align-items:center;font-family:"Oswald",sans-serif;font-size:15px;color:var(--white)}
.main-nav span{position:absolute;top:11px;letter-spacing:-.3px;text-transform:uppercase}

.info-box{left:16px;top:159px;width:223px;height:254px;background:var(--red);color:var(--white);padding:12px 14px}
.box-title{font-size:15px;letter-spacing:.2px}
.info-sub{font-size:15px;margin-top:14px}
.photo{display:block}
.info-photo{margin:6px 0 0 1px;width:191px;height:76px;background:linear-gradient(135deg,#c9c2b5,#e7d9c4 50%,#b56a5c);border:1px solid #e8c0c0}
.info-text{font-family:Arial,sans-serif;font-size:9.5px;line-height:13.7px;text-align:justify;margin-top:10px;padding:0 4px}

.hero{left:255px;top:159px;width:615px;height:254px;background:linear-gradient(100deg,#0f1a24,#24323e 45%,#141d26)}
.hero-slogan{right:36px;top:40px;text-align:right;color:var(--white);font-family:"Alfa Slab One",serif;font-size:31px;line-height:43px;transform:scaleX(.82);transform-origin:right}

.contact-form{left:16px;top:433px;width:223px;height:305px;background:var(--red-dark);border:1px dashed #d9a0a0;outline:2px solid var(--red-dark);color:var(--white);padding:12px 14px}
.contact-form .box-title{font-weight:700;font-size:15px}
.form-note{font-size:12px;margin:20px 0 8px 8px}
.field{height:24px;margin-bottom:12px;border-radius:3px;background:linear-gradient(#fafafa,#d6d6d6);color:#222;font-size:12px;padding:5px 8px}
.field.message{height:70px}
.submit{left:152px;top:282px;width:66px;height:24px;background:#0a0a0a;color:var(--white);font-size:12px;text-align:center;line-height:24px}

.content{left:257px;top:436px;width:613px;font-size:12px;line-height:20px}
.content h1{font-size:18.5px;color:var(--heading);font-weight:700;margin:0 0 10px -2px}
.content h2{font-size:16.5px;color:var(--heading);font-weight:700;margin:10px 0 0}
.content p{text-align:justify}
.content p+p{margin-top:20px}

.card{top:762px;width:298px;height:222px;background:linear-gradient(180deg,#c60a14,var(--card) 60%,#c00912);border-radius:6px;color:var(--white);padding:12px 20px 0;box-shadow:0 8px 8px -4px rgba(0,0,0,.45)}
.card h3{font-weight:400;font-size:25px;line-height:30px;margin-left:2px}
.card-photo{margin-top:6px;width:229px;height:57px}
.card p{font-family:Arial,sans-serif;font-size:10.8px;line-height:14.6px;text-align:justify;margin-top:10px;width:234px;margin-left:-2px}
.card .more{position:absolute;right:12px;bottom:8px;color:var(--yellow);font-family:Arial,sans-serif;font-size:11px}
.clip{position:absolute;top:-14px;width:12px;height:40px}

.site-footer{left:0;top:1026px;width:886px;height:131px;background:var(--red);color:var(--white);font-family:Arial,sans-serif;font-size:11px}
.footer-links{left:20px;top:18px}
.footer-links span{margin-right:10px}
.disclaimer{left:20px;top:53px;width:620px;line-height:16.5px}
.badge{left:770px;top:27px;width:93px;height:75px;background:#f5f5f5;box-shadow:8px 6px 0 rgba(255,255,255,.25)}
</style>
</head>
<body>
<div class="page">
  <header class="site-header abs">
    <div class="brand abs">
      <div class="brand-mark"></div>
      <div class="brand-name">
        <span class="small">LAW OFFICE OF</span>
        <span class="big">MARTA K. DOLVENIDZE</span>
      </div>
    </div>
    <div class="phone abs">
      <span class="phone-icon"><svg width="16" height="16" viewBox="0 0 24 24"><path fill="#8e1015" d="M6.6 10.8a15 15 0 0 0 6.6 6.6l2.2-2.2c.3-.3.7-.4 1-.2 1.1.4 2.3.6 3.6.6.6 0 1 .4 1 1V20c0 .6-.4 1-1 1A17 17 0 0 1 3 4c0-.6.4-1 1-1h3.5c.6 0 1 .4 1 1 0 1.3.2 2.5.6 3.6.1.3 0 .7-.2 1z"/></svg></span>
      415-555-0187
    </div>
  </header>

  <nav class="main-nav abs">
    <span style="left:77px">Home</span>
    <span style="left:173px">About Us</span>
    <span style="left:288px">Areas of Practice</span>
    <span style="left:451px">Resources</span>
    <span style="left:573px">Blog</span>
    <span style="left:660px">FAQ</span>
    <span style="left:736px">Contact Us</span>
  </nav>

  <section class="info-box abs">
    <svg class="clip" style="right:8px;top:-14px" viewBox="0 0 12 40"><path d="M3 34V6a3 3 0 0 1 6 0v30a4.5 4.5 0 0 1-9 0V10" fill="none" stroke="#bbb" stroke-width="1.4"/></svg>
    <div class="box-title">IMPORTANT INFORMATION</div>
    <div class="info-sub">chapter 7</div>
    <div class="photo info-photo" role="img" aria-label="Smiling family with children on bicycles"></div>
    <p class="info-text">Often called the liquidation chapter, or “fresh start,” chapter 7 is used by individuals, families, partnerships, or corporations whose financial difficulties do not allow them to repay all of their debts.</p>
  </section>

  <section class="hero abs" role="img" aria-label="Hand in a suit sleeve holding a small green seedling in soil">
    <div class="hero-slogan abs">Always<br>Protecting<br>CLIENT’S<br>INTERESTS!</div>
  </section>

  <form class="contact-form abs">
    <div class="box-title">CONTACT FORM</div>
    <div class="form-note">Fields marked with * are required.</div>
    <div class="field">Name *</div>
    <div class="field">Email *</div>
    <div class="field">Phone</div>
    <div class="field">Subject *</div>
    <div class="field message">Message *</div>
    <div class="submit abs">SUBMIT</div>
  </form>

  <article class="content abs">
    <h1>Welcome to BK Law Hub - Complete Bankruptcy Information</h1>
    <p>Gravel_-_main_pageThe Law Offices of Marta K. Dolvenidze is a consumer law office dedicated to consumer protection and zealously defending the rights of our clients. We offer the big firm quality legal representation with a small firm individualized attention to each client.</p>
    <p>Our office offers services in: all types of consumer bankruptcy filings, i.e. Chapter 7, Chapter 13, Chapter 11, negotiating a settlement of your debts, assisting you in the defense of collection litigation and defending you against foreclosure. Please review our site and see what we may be able to offer you. Feel free to call us at (415) 555-0187 or use our free case evaluation form.</p>
    <h2>Speak to a Lawyer</h2>
    <p>Unlike some other law firms, when you call the Law Office of Marta K. Dolvenidze you will speak to an actual attorney. Not a paralegal or assistant. And even after retaining our office you will still speak to an attorney unlike other firms where you cannot get a hold of your attorney after several attempts.</p>
  </article>

  <section class="card abs" style="left:17px">
    <svg class="clip" style="right:22px" viewBox="0 0 12 40"><path d="M3 34V6a3 3 0 0 1 6 0v30a4.5 4.5 0 0 1-9 0V10" fill="none" stroke="#bbb" stroke-width="1.4"/></svg>
    <h3>Debt Relief</h3>
    <div class="photo card-photo" role="img" aria-label="Lawyer consulting with a couple at a desk" style="background:linear-gradient(90deg,#4a4a52,#d8d2c8 55%,#8a7566)"></div>
    <p>This page is available, however, but because occasionally circumstances occur in which toil and pain can procure him some great. To take a trivial example, which of us ever undertakes laborious physical exercise, except to obtain some advantage from it.</p>
    <span class="more">read more...</span>
  </section>

  <section class="card abs" style="left:307px">
    <svg class="clip" style="right:22px" viewBox="0 0 12 40"><path d="M3 34V6a3 3 0 0 1 6 0v30a4.5 4.5 0 0 1-9 0V10" fill="none" stroke="#bbb" stroke-width="1.4"/></svg>
    <h3>Foreclosure Prevention</h3>
    <div class="photo card-photo" role="img" aria-label="Happy family of four in a car" style="background:linear-gradient(90deg,#3b3f46,#cbb8a4 50%,#6c727a)"></div>
    <p>This page is available, however, but because occasionally circumstances occur in which toil and pain can procure him some great. To take a trivial example, which of us ever undertakes laborious physical exercise, except to obtain some advantage from it.</p>
    <span class="more">read more...</span>
  </section>

  <section class="card abs" style="left:595px">
    <svg class="clip" style="right:22px" viewBox="0 0 12 40"><path d="M3 34V6a3 3 0 0 1 6 0v30a4.5 4.5 0 0 1-9 0V10" fill="none" stroke="#bbb" stroke-width="1.4"/></svg>
    <h3>Chapter 13</h3>
    <div class="photo card-photo" role="img" aria-label="Smiling couple relaxing at home with a laptop" style="background:linear-gradient(90deg,#e9e6e1,#d9b79a 50%,#ecebea)"></div>
    <p>This page is available, however, but because occasionally circumstances occur in which toil and pain can procure him some great. To take a trivial example, which of us ever undertakes laborious physical exercise, except to obtain some advantage from it.</p>
    <span class="more">read more...</span>
  </section>

  <footer class="site-footer abs">
    <div class="footer-links abs"><span>Go to top</span> Copyright © 2010 KDLaw. All Rights Reserved. | Web Development by Sitewright | Design by DMR</div>
    <p class="disclaimer abs">Disclaimer: The Law Offices of Marta K. Dolvenidze is a Debt Relief law firm as defined by 11 U.S.C. 528. We help people file for Bankruptcy Relief under the Bankruptcy Code. The information contained on this website is not to be construed as legal advice. It is not intended to solicit or form an attorney-client relationship. We do not guarantee any result and prior results do not guarantee a similar outcome. This is an attorney advertisement and this website is for informational purposes only.</p>
    <div class="badge abs" role="img" aria-label="Professional association membership badge"></div>
  </footer>
</div>
</body>
</html>
```